Digital Marketing Website Redesign, modern, fresh, dynamic

Hi there, we would like to freshen up our website and create a new dynamic look. We are a digital marketing agency who specialise in digital transformation in the form of creating websites for appointment bookings. Our clients are service businesses such as hairdressers, dentists and doctors who's patients need to book appointments with them.

Our company name is Tallomex with the point being we can help increase your revenue curve by increasing your appointment bookings.

Our services include building the website, creating campaigns to drive traffic, increasing conversions and monitoring and reporting.

We are playing with a tagline of 'Step into your Digital Transformation' as we have a 5 step journey that customers can take with us getting them from zero to full appointment bookings.

Our current website is www.tallomex-sample.com

You can see a draft design that I mocked up on Canva here https://www.draftboard-sample.com/design/QXB82LmpR7T/KpoW39dnFsYbZet_wqe_OPa/edit?utm_content=QXB82LmpR7T&utm_campaign=designshare&utm_medium=link2&utm_source=sharebutton

Also attached some other homepage ideas. In regard to photos we are open to ideas.

Please let if you need any more information to provide us with an initial design. Thanks million and I look forward to receiving fantastic designs :)

Marian Dobbs
Tallomex

Target Market(s)

Appointment based businesses such as hairdressers, dentists, doctors

Industry/Entity Type

Marketing and Digital

Coding

Coded - Design and coding required

Number of Pages Required

1 page

Colors
0094D4
00A9DD
6FCCEA
C7EBF8
E9F6FB

Requirements
Must have
• Appointment booking CTA
Nice to have
• A website we like https://www.fergalwhitty-sample.ie

```html
<!DOCTYPE html>
<html lang="en">
<head>
<meta charset="utf-8">
<title>Tallomex – Step into your Digital Transformation</title>
<link href="https://fonts.googleapis.com/css2?family=Ubuntu:wght@500;700&family=Lato:wght@400;700;900&display=swap" rel="stylesheet">
<style>
:root{
  --navy:#06193f;
  --navy-2:#1d3a6f;
  --heading:#1f3b73;
  --lime:#c6d600;
  --lime-dark:#aebd00;
  --ink:#2a2f3a;
  --muted:#8a8f99;
  --paper:#ffffff;
  --mist:#f3f4f6;
  --field:#3e5a8e;
}
*{box-sizing:border-box;margin:0;padding:0}
html,body{width:1200px;height:4307px;overflow:hidden}
body{position:relative;background:var(--paper);font-family:"Lato",sans-serif;color:var(--ink)}
.abs{position:absolute}
.section{position:absolute;left:0;width:1200px;overflow:hidden}
h1,h2,h3,h4{font-family:"Ubuntu",sans-serif;font-weight:700}
.eyebrow{font-family:"Lato",sans-serif;font-weight:700;color:var(--lime-dark);font-size:15px}
.btn-lime{position:absolute;background:var(--lime);color:#fff;font-weight:900;font-size:16px;display:flex;align-items:center;justify-content:center;gap:10px;border-radius:2px}

/* top bar */
.topbar{position:absolute;left:385px;top:0;width:815px;height:34px;background:var(--heading);color:#fff;font-size:11px;font-weight:700}
.topbar .item{position:absolute;top:0;height:34px;display:flex;align-items:center;gap:8px}
.topbar .appt{left:210px;width:231px;background:var(--lime);justify-content:center;text-transform:uppercase;font-size:10px}
.header{position:absolute;left:0;top:0;width:1200px;height:102px}
.brand{position:absolute;display:flex;align-items:center;gap:8px;font-family:"Ubuntu",sans-serif;font-weight:700;color:var(--heading)}
.brand .dot{width:12px;height:12px;border-radius:50%;background:var(--lime)}
.nav{position:absolute;top:60px;font-size:11px;color:var(--ink)}
.nav span{position:absolute;white-space:nowrap}
.btn-outline{position:absolute;left:932px;top:55px;width:118px;height:28px;border:1.5px solid var(--heading);border-radius:3px;font-size:10px;font-weight:900;color:var(--heading);display:flex;align-items:center;justify-content:center}

/* hero */
.hero{top:102px;height:717px;background:radial-gradient(ellipse at 50% 55%,#2a5d86 0%,#123252 40%,#061a33 80%)}
.hero .welcome{position:absolute;left:518px;top:199px;width:161px;height:33px;background:#1f3f8a;color:#fff;font-size:11px;font-weight:900;display:flex;align-items:center;justify-content:center}
.hero h1{position:absolute;left:0;width:1200px;top:244px;text-align:center;color:#fff;font-size:62px;line-height:70px}
.hero .more{position:absolute;left:517px;top:416px;width:164px;height:45px;border:1.5px solid #d7e2ef;border-radius:3px;color:#fff;font-size:11px;font-weight:900;display:flex;align-items:center;justify-content:center}

/* about */
.about{top:819px;height:597px}
.about h2{position:absolute;left:640px;top:96px;font-size:47px;line-height:57px;color:var(--heading);font-weight:500}
.about p{position:absolute;left:640px;top:215px;width:455px;font-size:14px;line-height:24px;color:var(--muted)}

/* services */
.services{top:1416px;height:671px;background:var(--navy)}
.services h2{position:absolute;left:0;width:1200px;top:134px;text-align:center;color:#fff;font-size:45px;font-weight:500}
.card{position:absolute;top:299px;width:318px}
.card .photo{height:241px;background:linear-gradient(160deg,#c9ced6,#4e5a6a)}
.card .label{position:absolute;left:14px;right:14px;top:208px;height:78px;background:#fff;text-align:center;padding-top:14px}
.card .label h3{font-size:18px;color:var(--heading);font-weight:500}
.card .label span{display:block;margin-top:8px;font-size:13px;color:var(--muted)}
.card .badge{position:absolute;left:111px;top:-55px}

/* excellence */
.excellence{top:2087px;height:593px;background:var(--mist)}
.excellence h2{position:absolute;left:105px;top:88px;font-size:36px;line-height:44px;color:var(--heading);font-weight:500}
.tab{position:absolute;top:203px;height:44px;border-radius:3px;background:#fff;font-size:16px;color:var(--muted);display:flex;align-items:center;padding-left:16px;box-shadow:0 1px 3px rgba(0,0,0,.08)}
.tab.active{background:var(--lime);color:#fff;font-weight:700}
.excellence p{position:absolute;left:368px;top:290px;width:320px;font-size:13.5px;line-height:24px;color:var(--muted)}
.checks{position:absolute;left:366px;top:428px;font-size:13.5px;color:var(--muted);list-style:none}
.checks li{display:flex;align-items:center;gap:10px;height:33.5px}

/* contact */
.contact{top:2680px;height:435px;background:linear-gradient(90deg,#1b2f5e,#283f78 60%,#1a2d5c)}
.contact h2{position:absolute;left:109px;top:141px;color:#fff;font-size:48px;line-height:57px;font-weight:500}
.contact h3{position:absolute;left:692px;width:393px;top:82px;text-align:center;color:#fff;font-family:"Lato",sans-serif;font-size:21px;font-weight:700}
.field{position:absolute;left:692px;width:393px;height:46px;background:var(--field);border-radius:5px;color:#fff;font-size:12px;font-weight:900;display:flex;align-items:center;padding-left:52px}
.submit{position:absolute;left:692px;top:326px;width:393px;height:46px;background:var(--lime);border-radius:5px;color:#fff;font-size:14px;font-weight:900;display:flex;align-items:center;justify-content:center}

/* testimonials */
.reviews{top:3115px;height:647px;background:var(--mist)}
.reviews h2{position:absolute;left:0;width:1200px;top:122px;text-align:center;color:var(--heading);font-size:46px;font-weight:500}
.review .avatar{position:absolute;width:87px;height:120px;background:linear-gradient(180deg,#d8dde4,#5d6a7b)}
.review h4{position:absolute;font-size:18px;color:var(--heading);font-weight:500}
.review .city{position:absolute;font-size:12px;color:var(--muted)}
.review .box{position:absolute;width:301px;height:167px;background:#fff;box-shadow:0 4px 14px rgba(0,0,0,.06);padding:38px 32px 0 34px;font-size:14px;line-height:24px;color:var(--muted)}
.review .quote{position:absolute;font-family:"Ubuntu",sans-serif;font-size:64px;line-height:1;color:var(--lime);font-weight:700}

/* footer */
.footer{top:3762px;height:545px}
.footer .col-title{position:absolute;top:224px;color:#fff;font-size:20px;font-family:"Lato",sans-serif;font-weight:700}
.footer .small{position:absolute;color:#fff;font-size:12px;font-weight:700;line-height:25px}
.social{position:absolute;top:386px;width:30px;height:30px;border-radius:3px;border:1px solid #8aa0c6;display:flex;align-items:center;justify-content:center}
.social i{width:10px;height:10px;background:#fff;border-radius:50%;display:block}
.subscribe{position:absolute;left:518px;top:351px;width:223px;height:42px;background:var(--field);border-radius:4px;color:#fff;font-size:12px;font-weight:700;display:flex;align-items:center;justify-content:space-between;padding:0 14px}
.contact-item h4{position:absolute;color:#fff;font-family:"Lato",sans-serif;font-size:17px;font-weight:700}
.contact-item span{position:absolute;color:#fff;font-size:13px;font-weight:700}
.rule{position:absolute;left:95px;top:480px;width:1009px;height:1px;background:#4a6496}
.copyright{position:absolute;left:0;width:1200px;top:503px;text-align:center;color:#fff;font-size:13px;font-weight:700}
.to-top{position:absolute;left:1063px;top:493px;width:34px;height:34px;background:var(--lime);display:flex;align-items:center;justify-content:center}
</style>
</head>
<body>

<!-- header -->
<header class="header">
  <div class="topbar">
    <div class="item" style="left:60px">
      <svg width="12" height="12" viewBox="0 0 24 24" fill="none" stroke="#fff" stroke-width="2"><path d="M5 3h4l2 5-3 2a12 12 0 006 6l2-3 5 2v4a2 2 0 01-2 2A17 17 0 013 5a2 2 0 012-2z"/></svg>
      555 - 010 - 4821
    </div>
    <div class="item appt">
      <svg width="14" height="11" viewBox="0 0 24 18" fill="none" stroke="#fff" stroke-width="2"><rect x="1" y="1" width="22" height="16" rx="2"/><path d="M1 2l11 8 11-8"/></svg>
      Request an appointment
    </div>
    <div class="item" style="left:475px;font-size:10px">
      <svg width="11" height="13" viewBox="0 0 20 24" fill="none" stroke="#fff" stroke-width="2"><path d="M10 23s8-8 8-13a8 8 0 00-16 0c0 5 8 13 8 13z"/><circle cx="10" cy="10" r="3"/></svg>
      88 Harbour Lane Dunmore
    </div>
  </div>
  <div class="brand" style="left:133px;top:36px;font-size:34px">Tallomex<span class="dot"></span></div>
  <nav class="nav">
    <span style="left:365px;font-weight:900">HOME</span>
    <span style="left:468px">About Us</span>
    <span style="left:591px">Services</span>
    <span style="left:697px">Our Team</span>
    <span style="left:790px">Projects</span>
  </nav>
  <div class="btn-outline">CONTACT US</div>
</header>

<!-- hero -->
<section class="section hero">
  <div role="img" aria-label="Person walking down a glowing digital tunnel" class="abs" style="left:0;top:0;width:1200px;height:717px;background:radial-gradient(ellipse at 50% 60%,rgba(120,190,220,.35),transparent 45%)"></div>
  <div class="welcome">WELCOME</div>
  <h1>Step into your<br>Digital Transformation</h1>
  <div class="more">LEARN MORE</div>
  <svg class="abs" style="left:0;top:0" width="1200" height="717" viewBox="0 0 1200 717">
    <path d="M0 525 C300 700 880 760 1200 533 L1200 717 L0 717 Z" fill="#fff"/>
    <path d="M0 525 C140 600 300 650 440 683 C300 660 130 630 0 600 Z" fill="var(--lime)"/>
    <path d="M1200 533 C1140 590 1080 630 1020 663 C1090 640 1160 610 1200 585 Z" fill="var(--lime)"/>
  </svg>
</section>

<!-- about -->
<section class="section about">
  <svg class="abs" style="left:87px;top:39px" width="502" height="502" viewBox="0 0 502 502">
    <g role="img" aria-label="Collage of team members working with technology">
      <rect x="0" y="0" width="160" height="160" transform="translate(251 12) rotate(45)" fill="#6f7f96"/>
      <rect x="0" y="0" width="160" height="160" transform="translate(132 131) rotate(45)" fill="#c8b39a"/>
      <rect x="0" y="0" width="160" height="160" transform="translate(370 131) rotate(45)" fill="#45546a"/>
      <rect x="0" y="0" width="160" height="160" transform="translate(251 250) rotate(45)" fill="#8a9bb3"/>
    </g>
    <circle cx="251" cy="244" r="48" fill="#fff"/>
    <text x="251" y="249" text-anchor="middle" font-family="Ubuntu,sans-serif" font-weight="700" font-size="17" fill="#1f3b73">Tallomex</text>
  </svg>
  <div class="eyebrow abs" style="left:640px;top:69px">About Us</div>
  <h2>Online Presence,<br>Unleashed Potential</h2>
  <p>Lorem ipsum dolor sit amet, consectetur adipiscing elit, sed do eiusmod tempor incididunt ut labore et dolore magna aliqua. Ut en im ad minim veniam, quis nostrud exercitation ullamco laboris nisi ut aliquip ex ea commodo consequat. Duis aute irure dolor in repr ehenderit in voluptate velit esse cillum dolore eu fugiat nulla pariatur. Excepteur sint occaecat cupidatat non proident, sunt in culpa qui officia deserunt mollit. ehenderit in voluptate velit esse cillum dolore eu fugiat nulla pariatur. Excepteur sint occaecat cup idatat non proident, sunt in culpa qui officia.</p>
  <div class="btn-lime" style="left:640px;top:455px;width:154px;height:45px">Learn More
    <svg width="16" height="12" viewBox="0 0 16 12" fill="none" stroke="#fff" stroke-width="2"><path d="M0 6h14M9 1l5 5-5 5"/></svg>
  </div>
</section>

<!-- services -->
<section class="section services">
  <div class="eyebrow abs" style="left:0;width:1200px;top:105px;text-align:center;color:var(--lime)">Services</div>
  <h2>Our Services</h2>

  <div class="card" style="left:95px">
    <div class="photo" role="img" aria-label="Hands on a laptop with floating document icons"></div>
    <div class="label"><h3>Marketing Services</h3><span>Read More &rsaquo;</span></div>
    <svg class="badge" width="96" height="96" viewBox="0 0 96 96"><path d="M3 48a45 45 0 0190 0" fill="none" stroke="#fff" stroke-width="1"/><circle cx="48" cy="50" r="40" fill="var(--lime)"/><path d="M48 36l12 9-5 14H41l-5-14z" fill="none" stroke="#fff" stroke-width="2.5"/></svg>
  </div>
  <div class="card" style="left:441px">
    <div class="photo" role="img" aria-label="Colleagues reviewing a booking app on a monitor"></div>
    <div class="label"><h3>Online Booking Apps</h3><span>Read More &rsaquo;</span></div>
    <svg class="badge" width="96" height="96" viewBox="0 0 96 96"><path d="M3 48a45 45 0 0190 0" fill="none" stroke="#fff" stroke-width="1"/><circle cx="48" cy="50" r="40" fill="var(--lime)"/><circle cx="48" cy="52" r="14" fill="none" stroke="#fff" stroke-width="2.5"/><path d="M48 52l7-7" stroke="#fff" stroke-width="2.5"/></svg>
  </div>
  <div class="card" style="left:786px">
    <div class="photo" role="img" aria-label="Hand holding a glowing digital globe"></div>
    <div class="label"><h3>Services Marketing</h3><span>Read More &rsaquo;</span></div>
    <svg class="badge" width="96" height="96" viewBox="0 0 96 96"><path d="M3 48a45 45 0 0190 0" fill="none" stroke="#fff" stroke-width="1"/><circle cx="48" cy="50" r="40" fill="var(--lime)"/><path d="M36 62h24M40 62l10-20 6 4-8 16" fill="none" stroke="#fff" stroke-width="2.5"/></svg>
  </div>
</section>

<!-- excellence -->
<section class="section excellence">
  <h2>Digital Excellence,<br>Marketing Brilliance</h2>
  <div class="tab active" style="left:107px;width:159px">Our Mission</div>
  <div class="tab" style="left:281px;width:160px">Our Vision</div>
  <div class="tab" style="left:463px;width:149px">Our awards</div>
  <div role="img" aria-label="Technician with a laptop in a server room" class="abs" style="left:105px;top:292px;width:223px;height:228px;border-radius:6px;background:linear-gradient(160deg,#3e5578,#121f36)"></div>
  <p>Lorem ipsum dolor sit amet, consectetur eiusmod tempor incididunt ut labore et dolore im ad minim veniam, quis nostrud exercitation eiusmod tempor incididunt ut labore et dolore im ad minim veniam, quis nostrud exercitation</p>
  <ul class="checks">
    <li><svg width="15" height="15" viewBox="0 0 16 16" fill="none" stroke="var(--lime)" stroke-width="1.6"><rect x="1" y="1" width="14" height="14"/><path d="M4 8l3 3 6-7"/></svg>Award winning company</li>
    <li><svg width="15" height="15" viewBox="0 0 16 16" fill="none" stroke="var(--lime)" stroke-width="1.6"><rect x="1" y="1" width="14" height="14"/><path d="M4 8l3 3 6-7"/></svg>Award winning company</li>
    <li><svg width="15" height="15" viewBox="0 0 16 16" fill="none" stroke="var(--lime)" stroke-width="1.6"><rect x="1" y="1" width="14" height="14"/><path d="M4 8l3 3 6-7"/></svg>Award winning company</li>
  </ul>
  <div role="img" aria-label="Two business colleagues looking at a tablet together" class="abs" style="left:786px;top:45px;width:414px;height:548px;background:linear-gradient(180deg,#e4e6ea 0%,#9aa0aa 45%,#2a2e36 100%);border-radius:180px 180px 0 0"></div>
</section>

<!-- contact -->
<section class="section contact">
  <div role="img" aria-label="Blurred server room backdrop" class="abs" style="left:0;top:0;width:1200px;height:435px;background:radial-gradient(ellipse at 30% 50%,rgba(90,120,180,.25),transparent 60%)"></div>
  <h2>Crafting Your<br>Success Story in the<br>Digital World</h2>
  <h3>Get in touch with us</h3>
  <div class="field" style="top:129px">Full Name</div>
  <div class="field" style="top:196px">Email Address</div>
  <div class="field" style="top:261px">Industry</div>
  <div class="submit">SUBMIT</div>
</section>

<!-- testimonials -->
<section class="section reviews">
  <div class="eyebrow abs" style="left:0;width:1200px;top:92px;text-align:center">Testimonials</div>
  <h2>Clients Reviews</h2>

  <div class="review">
    <div class="avatar" role="img" aria-label="Portrait of a client" style="left:92px;top:226px"></div>
    <h4 style="left:204px;top:246px">Oliver Brannick</h4>
    <span class="city" style="left:206px;top:277px">Brussels</span>
    <div class="box" style="left:112px;top:326px">Lorem ipsum dolor sit amet, consect etur adipiscing elit, sed do eiusmod tempor incididunt ut labore et dolore magna aliqua. Ut enim ad minim veni am, quis nostrud</div>
    <div class="quote" style="left:356px;top:315px">&ldquo;</div>
  </div>
  <div class="review">
    <div class="avatar" role="img" aria-label="Portrait of a client" style="left:438px;top:226px"></div>
    <h4 style="left:545px;top:246px">Lena Marsh</h4>
    <span class="city" style="left:547px;top:277px">Brussels</span>
    <div class="box" style="left:460px;top:326px">Lorem ipsum dolor sit amet, consect etur adipiscing elit, sed do eiusmod tempor incididunt ut labore et dolore magna aliqua. Ut enim ad minim veni am, quis nostrud</div>
    <div class="quote" style="left:704px;top:315px">&ldquo;</div>
  </div>
  <div class="review">
    <div class="avatar" role="img" aria-label="Portrait of a client" style="left:788px;top:226px"></div>
    <h4 style="left:886px;top:246px">Samuel Okoro</h4>
    <span class="city" style="left:888px;top:277px">Brussels</span>
    <div class="box" style="left:808px;top:326px">Lorem ipsum dolor sit amet, consect etur adipiscing elit, sed do eiusmod tempor incididunt ut labore et dolore magna aliqua. Ut enim ad minim veni am, quis nostrud</div>
    <div class="quote" style="left:1052px;top:315px">&ldquo;</div>
  </div>

  <div class="btn-lime" style="left:522px;top:568px;width:154px;height:46px">Learn More
    <svg width="16" height="12" viewBox="0 0 16 12" fill="none" stroke="#fff" stroke-width="2"><path d="M0 6h14M9 1l5 5-5 5"/></svg>
  </div>
</section>

<!-- footer -->
<footer class="section footer">
  <svg class="abs" style="left:0;top:0" width="1200" height="545" viewBox="0 0 1200 545">
    <rect width="1200" height="545" fill="var(--mist)"/>
    <path d="M0 190 C300 0 900 -20 1200 150 L1200 545 L0 545 Z" fill="var(--navy-2)"/>
    <path d="M0 190 C120 120 280 70 440 40 C280 90 130 160 0 230 Z" fill="var(--lime)"/>
    <path d="M1200 150 C1130 110 1070 80 1000 60 C1080 100 1150 150 1200 200 Z" fill="var(--lime)"/>
  </svg>
  <div class="brand" style="left:122px;top:212px;font-size:32px;color:#fff">Tallomex<span class="dot"></span></div>
  <div class="small" style="left:112px;top:296px;width:210px">Subscribe to our newsletter to recieve updates or the latest news</div>
  <div class="social" style="left:114px"><i></i></div>
  <div class="social" style="left:154px"><i></i></div>
  <div class="social" style="left:196px"><i></i></div>
  <div class="social" style="left:236px"><i></i></div>

  <div class="col-title" style="left:518px">Newsletter</div>
  <div class="small" style="left:518px;top:269px;width:215px">Subscribe to our newsletter to recieve updates or the latest news</div>
  <div class="subscribe">Subscribe with us
    <svg width="8" height="13" viewBox="0 0 8 13" fill="none" stroke="#fff" stroke-width="2"><path d="M1 1l5 5.5L1 12"/></svg>
  </div>

  <div class="col-title" style="left:861px">Contacts</div>
  <div class="contact-item">
    <svg class="abs" style="left:862px;top:264px" width="34" height="36" viewBox="0 0 34 36" fill="none" stroke="var(--lime)" stroke-width="1.6"><rect x="3" y="2" width="16" height="30" rx="2"/><path d="M9 28h4M24 12a6 6 0 010 10M28 9a10 10 0 010 16"/></svg>
    <h4 style="left:907px;top:260px">Contact Us</h4>
    <span style="left:907px;top:288px">(44) 555-010-372</span>
  </div>
  <div class="contact-item">
    <svg class="abs" style="left:862px;top:337px" width="34" height="34" viewBox="0 0 34 34" fill="none" stroke="var(--lime)" stroke-width="1.6"><rect x="2" y="8" width="30" height="22"/><path d="M2 8l15 12 15-12M2 30l11-10M32 30L21 20"/></svg>
    <h4 style="left:907px;top:333px">Contact Us</h4>
    <span style="left:907px;top:361px">(44) 555-010-372</span>
  </div>

  <div class="rule"></div>
  <div class="copyright">Tallomex</div>
  <div class="to-top">
    <svg width="14" height="9" viewBox="0 0 14 9" fill="none" stroke="#fff" stroke-width="2"><path d="M1 8l6-6 6 6"/></svg>
  </div>
</footer>

</body>
</html>
```